Im open to ideas.. I was thinking on my business cards aswell as my logo. a place for my name. email. phone number and abn..

ive attched a file with my business logo. which i dont love the colours.. i was think a dark background with charcoal letters so something along those colour schumes but im open to ideas..

BRM Constructions

```html
<!DOCTYPE html>
<html lang="en">
<head>
<meta charset="UTF-8">
<title>BRM Constructions – Business Card</title>
<link href="https://fonts.googleapis.com/css2?family=Roboto:wght@400;500;700&display=swap" rel="stylesheet">
<style>
  :root {
    --charcoal: #231f20;
    --brand-red: #ed1c24;
    --paper: #ffffff;
    --ink: #231f20;
    --muted: #555555;
    --backdrop: #e4e1dc;
  }
  * { box-sizing: border-box; margin: 0; padding: 0; }
  html, body {
    width: 1200px;
    height: 987px;
    overflow: hidden;
    background: var(--backdrop);
    font-family: "Roboto", Arial, sans-serif;
  }
  .canvas {
    position: relative;
    width: 1200px;
    height: 987px;
  }
  .card {
    position: absolute;
    left: 306px;
    width: 615px;
    height: 352px;
    background: var(--paper);
    overflow: hidden;
  }
  .card--front { top: 130px; }
  .card--back { top: 505px; }

  .front-header {
    position: absolute;
    left: 0; top: 0;
    width: 100%;
    height: 235px;
    background: var(--charcoal);
  }
  .front-band {
    position: absolute;
    left: 0; top: 235px;
    width: 100%;
    height: 16px;
    background: var(--brand-red);
  }
  .wordmark {
    position: absolute;
    font-weight: 700;
    text-transform: uppercase;
    letter-spacing: 1px;
    white-space: nowrap;
  }
  .wordmark--front {
    right: 52px;
    top: 82px;
    font-size: 34px;
    color: var(--paper);
  }
  .wordmark--back {
    left: 0; right: 0;
    top: 150px;
    text-align: center;
    font-size: 46px;
    color: var(--ink);
  }

  .holder {
    position: absolute;
    left: 35px;
    top: 262px;
  }
  .holder-name {
    font-size: 22px;
    font-weight: 500;
    color: var(--brand-red);
    line-height: 1.2;
  }
  .holder-role {
    font-size: 16px;
    color: var(--ink);
    margin-top: 4px;
  }
  .holder-abn {
    font-size: 15px;
    color: var(--muted);
    letter-spacing: 0.5px;
    margin-top: 8px;
  }

  .contact {
    position: absolute;
    right: 36px;
    top: 268px;
    list-style: none;
    text-align: right;
  }
  .contact-item {
    display: flex;
    justify-content: flex-end;
    align-items: center;
    gap: 8px;
    font-size: 15px;
    color: var(--ink);
    height: 23px;
  }
  .contact-item--web {
    color: var(--brand-red);
    letter-spacing: 1px;
    padding-right: 0;
  }
  .contact-icon {
    width: 16px;
    height: 14px;
    flex: none;
  }
</style>
</head>
<body>
<main class="canvas">

  <section class="card card--front" aria-label="Business card front">
    <div class="front-header"></div>
    <div class="front-band"></div>
    <div class="wordmark wordmark--front">BRM Constructions</div>

    <div class="holder">
      <p class="holder-name">Sam Carter</p>
      <p class="holder-role">President</p>
      <p class="holder-abn">ABN: 987654321</p>
    </div>

    <ul class="contact">
      <li class="contact-item">555 0142 7781
        <svg class="contact-icon" viewBox="0 0 16 14" aria-hidden="true">
          <path d="M1 4 Q8 -1 15 4 L13 6 L11 4.5 L5 4.5 L3 6 Z" fill="var(--brand-red)"/>
          <path d="M4 7 L12 7 L14 13 L2 13 Z" fill="var(--brand-red)"/>
          <circle cx="8" cy="10" r="1.8" fill="var(--paper)"/>
        </svg>
      </li>
      <li class="contact-item">sam@brmbuild.com
        <svg class="contact-icon" viewBox="0 0 16 14" aria-hidden="true">
          <rect x="1" y="3" width="14" height="9" fill="var(--brand-red)"/>
          <path d="M1 3 L8 8.5 L15 3" fill="none" stroke="var(--paper)" stroke-width="1.2"/>
        </svg>
      </li>
      <li class="contact-item contact-item--web">www.brmbuild.com</li>
    </ul>
  </section>

  <section class="card card--back" aria-label="Business card back">
    <div class="wordmark wordmark--back">BRM Constructions</div>
  </section>

</main>
</body>
</html>
```